ORLA - Óptica Médica - web design and concept

Website concept - Create and develop our website design and structure. ORLA is an optical store chain, and we are looking to establish our web and digital concept. In attachment there are several pictures about our stores and our logo.

The website structure should be user friendly. Colors should be light and the design as simple and minimalist as possible. There are different variations of the logothat can be used, check the file.

The website will include optical collections and sun collections as an online store. Also, a medical menu should be considered in order for clients to schedule optometry appointments. There should also be a menu for client assistance where the clients can read about glass maintenance in our workshop.
Updates

Low design quality

Number of Pages Required

5+ page

Font styles to use
Serif
Sans Serif

Requirements
Must have
• Must be user-friendly and minimalist.
• Please USE PICTURES FROM THE BRANDS we sell: MERUN, BOSKA, PNW, KOLE, BAMPE
Nice to have
• Nice to inspire: ZEK glasses (see website https://ch.shopzek.com/en/)
• Nice to inspire: https://merun-eyewear.com/
• Nice to ispire: https://www.pnwglobe.com/en/
Should not have
• Hysteric colors and shapes

```html
<!DOCTYPE html>
<html lang="en">
<head>
<meta charset="utf-8">
<title>ORLA Óptica Médica</title>
<link href="https://fonts.googleapis.com/css2?family=PT+Serif:wght@400;700&family=Roboto:wght@400;500;700&family=Roboto+Condensed:wght@400;700&display=swap" rel="stylesheet">
<style>
:root{
  --gold:#d3a14a;
  --gold-soft:#e2bf7d;
  --ink:#1f1c1c;
  --text:#555;
  --muted:#8a8a8a;
  --blush:#f5f1f1;
  --band:#f4f1f1;
  --footer:#f4f4f4;
  --dark:#231f20;
  --line:#e6e1d8;
  --white:#fff;
}
*{box-sizing:border-box;margin:0;padding:0}
html,body{width:1200px;height:2590px;overflow:hidden}
body{position:relative;background:var(--white);font-family:"Roboto",Arial,sans-serif;color:var(--text)}
.abs{position:absolute}
.btn{position:absolute;display:flex;align-items:center;justify-content:center;background:var(--gold);color:var(--white);border-radius:20px;font:700 11px "Roboto Condensed",Arial,sans-serif;text-transform:uppercase;letter-spacing:.3px}
.serif{font-family:"PT Serif",Georgia,serif}

/* nav */
.topbar{position:absolute;left:0;top:0;width:1200px;height:30px;background:var(--dark);color:var(--white);font:700 11px "Roboto",Arial,sans-serif}
.topbar span{position:absolute;top:8px}
.topbar svg{position:absolute;top:7px}

/* hero */
.hero{position:absolute;left:0;top:30px;width:1200px;height:510px;background:var(--blush);overflow:hidden}
.hero-photo{position:absolute;left:400px;top:0;width:800px;height:510px;background:linear-gradient(90deg,rgba(245,241,241,1) 0%,rgba(210,208,206,.6) 20%,#b9b6b2 40%,#8e8780 65%,#c9b59a 100%)}
.hero-ghost{position:absolute;font:400 110px "PT Serif",Georgia,serif;color:rgba(211,161,74,.08)}
.brand{position:absolute;text-align:center;color:var(--gold)}
.brand .name{font:400 44px "PT Serif",Georgia,serif;letter-spacing:6px}
.brand .sub{font:400 11px "Roboto",Arial,sans-serif;letter-spacing:4px;margin-top:2px}
.hero-title{left:160px;top:236px;font:700 38px "PT Serif",Georgia,serif;color:var(--gold)}
.hero-sub{left:160px;top:280px;font:700 29px "PT Serif",Georgia,serif;color:var(--gold)}

/* about */
.frame{position:absolute;border:5px solid var(--gold)}
.photo-box{position:absolute;border:6px solid var(--white);box-shadow:0 0 8px rgba(0,0,0,.12)}
.section-title{position:absolute;font:400 31px "PT Serif",Georgia,serif;color:var(--ink)}
.para{position:absolute;font:400 11.5px/1.6 "Roboto",Arial,sans-serif;color:var(--text)}

/* features */
.features{position:absolute;left:0;top:1100px;width:1200px;height:257px;background:var(--band)}
.feature{position:absolute;top:0;width:300px}
.feature .num{position:absolute;top:20px;font:700 76px "PT Serif",Georgia,serif;color:rgba(0,0,0,.035)}
.feature .title{position:absolute;top:118px;font:700 16px "PT Serif",Georgia,serif;color:var(--ink);letter-spacing:.4px;white-space:nowrap}
.feature .desc{position:absolute;top:144px;font:400 11px "Roboto",Arial,sans-serif;color:var(--muted);white-space:nowrap}
.feature .btn{top:180px;width:80px;height:30px;left:0}

/* brands */
.brands{position:absolute;left:0;top:1357px;width:1200px;height:123px;border-bottom:2px solid var(--line)}
.brands span{position:absolute;top:52px;transform:translateX(-50%);font:700 18px "Roboto",Arial,sans-serif;color:var(--ink);letter-spacing:1px;white-space:nowrap}

/* store */
.card{position:absolute;top:1608px;width:190px}
.card .img{width:190px;height:164px;background:#f1f1f1;border:4px solid #fafafa;box-shadow:0 0 0 1px #e4e4e4}
.card .label{position:absolute;top:182px;left:0;font:700 10px "Roboto Condensed",Arial,sans-serif;color:var(--ink);text-transform:uppercase}
.card .price{position:absolute;top:223px;left:0;font:400 13px "PT Serif",Georgia,serif;color:var(--ink)}
.card .cart{position:absolute;top:217px;right:0;width:28px;height:28px;border-radius:3px;background:#ececec;display:flex;align-items:center;justify-content:center}
.card .rule{position:absolute;top:256px;left:0;width:190px;height:2px;background:#e5e5e5}
.card.active .price{color:var(--gold)}
.card.active .cart{background:var(--gold)}

/* tabs */
.tab{position:absolute;top:2002px;font:700 11px "Roboto Condensed",Arial,sans-serif;padding-bottom:6px}

/* footer */
.footer{position:absolute;left:0;top:2297px;width:1200px;height:242px;background:var(--footer)}
.foot-head{position:absolute;font:700 14px "PT Serif",Georgia,serif;color:var(--ink)}
.foot-line{position:absolute;font:400 10.5px/1.6 "Roboto",Arial,sans-serif;color:var(--text)}
.social{position:absolute;top:2385px;display:flex;gap:6px}
.social span{display:flex;align-items:center;justify-content:center;height:36px;padding:0 7px;background:var(--gold);color:var(--white);font:500 10px "Roboto",Arial,sans-serif}
.bottombar{position:absolute;left:0;top:2539px;width:1200px;height:51px;background:var(--dark);color:var(--white);font:400 10.5px "Roboto",Arial,sans-serif;display:flex;align-items:center;justify-content:center}
</style>
</head>
<body>

<header class="topbar">
  <span style="left:160px">Start</span>
  <span style="left:221px">About Us</span>
  <span style="left:304px">Products</span>
  <span style="left:385px">Contact Us</span>
  <span style="left:477px">Blogs</span>
  <span style="left:542px">Store</span>
  <svg style="left:846px" width="13" height="14" viewBox="0 0 13 14"><circle cx="6.5" cy="4" r="3.2" fill="#fff"/><path d="M0.5 14c0-4 2.7-6 6-6s6 2 6 6z" fill="#fff"/></svg>
  <span style="left:864px">Sign In</span>
  <svg style="left:906px" width="15" height="15" viewBox="0 0 15 15"><circle cx="7.5" cy="7.5" r="6.5" fill="none" stroke="#fff" stroke-width="1.4"/><path d="M1 7.5h13M7.5 1c-3 3.5-3 9.5 0 13M7.5 1c3 3.5 3 9.5 0 13" fill="none" stroke="#fff" stroke-width="1"/></svg>
  <span style="left:926px">Language</span>
  <svg style="left:1022px;top:5px" width="16" height="18" viewBox="0 0 16 18"><rect x="1" y="5" width="12" height="12" rx="1" fill="none" stroke="#fff" stroke-width="1.5"/><path d="M4 5V3.5a3 3 0 0 1 6 0V5" fill="none" stroke="#fff" stroke-width="1.5"/><circle cx="12.5" cy="14" r="3" fill="#d3a14a"/></svg>
</header>

<section class="hero">
  <div class="hero-photo" role="img" aria-label="Store interior with wooden central counter, gold-framed display cabinets and a geometric chandelier"></div>
  <div class="hero-ghost" style="left:-20px;top:160px">ORLA</div>
  <div class="hero-ghost" style="left:245px;top:370px">ORLA</div>
  <div class="brand" style="left:160px;top:78px;width:140px">
    <div class="name">ORLA</div>
    <div class="sub">ÓPTICA MÉDICA</div>
  </div>
  <h1 class="abs hero-title">ORLA OPTICA</h1>
  <p class="abs hero-sub">Our priority is your visual health</p>
  <a class="btn" style="left:160px;top:329px;width:127px;height:37px">Learn more</a>
</section>

<section class="about">
  <div class="frame" style="left:262px;top:644px;width:256px;height:363px;border-left:none;border-top:none"></div>
  <div class="frame" style="left:262px;top:644px;width:256px;height:363px;border-bottom:5px solid var(--gold);border-right:5px solid var(--gold);border-top:5px solid var(--gold);border-left:5px solid var(--gold);clip-path:polygon(0 85%,0 100%,100% 100%,100% 0,85% 0,85% 85%)"></div>
  <div class="photo-box" style="left:190px;top:601px;width:288px;height:349px;background:linear-gradient(180deg,#dcdcdc 0%,#9a948c 45%,#a47a52 70%,#eae6e0 100%)" role="img" aria-label="Store interior with central wooden counter and display walls"></div>
  <div class="abs" style="left:415px;top:935px;width:260px;height:95px;border-radius:50%;background:radial-gradient(ellipse,#b9a0c9 0%,#d8c6e0 45%,rgba(255,255,255,0) 72%)" role="img" aria-label="Glass bottle with dried lavender flowers"></div>
  <h2 class="section-title" style="left:590px;top:617px">ORLA OPTICS</h2>
  <p class="para" style="left:590px;top:672px;font-weight:700;font-style:italic;color:var(--ink)">ORLA OPTICA opens its doors with a clear purpose: to take care of you.</p>
  <p class="para" style="left:590px;top:720px;width:430px">Our priority is your visual health, and for this reason we have the best professionals and the most competitive products to serve your needs.</p>
  <p class="para" style="left:590px;top:768px;width:430px">Orla Óptica is the dream of a young entrepreneur named Mateo. With a degree in optics and optometry, he has acquired knowledge</p>
  <p class="para" style="left:590px;top:818px;width:470px">and skills to provide that multidisciplinary and demanding service that you deserve.</p>
  <a class="btn" style="left:590px;top:881px;width:172px;height:36px">Get to know us better</a>
</section>

<section class="features">
  <svg class="abs" style="left:112px;top:119px" width="10" height="16" viewBox="0 0 10 16"><path d="M8 2L2 8l6 6" fill="none" stroke="#222" stroke-width="2"/></svg>
  <svg class="abs" style="left:1076px;top:119px" width="10" height="16" viewBox="0 0 10 16"><path d="M2 2l6 6-6 6" fill="none" stroke="#222" stroke-width="2"/></svg>
  <div class="feature" style="left:160px">
    <div class="num">01</div>
    <div class="title">ORLA CHILDHOOD GUARANTEE</div>
    <div class="desc">50% discount on new glasses, if your child's graduation</div>
    <a class="btn">More</a>
  </div>
  <div class="feature" style="left:482px">
    <div class="num">02</div>
    <div class="title">ORLA ACCIDENT WARRANTY</div>
    <div class="desc">Did you get off your glasses when you got out of</div>
    <a class="btn">More</a>
  </div>
  <div class="feature" style="left:801px">
    <div class="num">03</div>
    <div class="title">ORLA SECURITY</div>
    <div class="desc">If you have suffered a robbery or robbery in your</div>
    <a class="btn">More</a>
  </div>
</section>

<section class="brands">
  <span style="left:254px">WARDEN</span>
  <span style="left:427px;font-weight:400">LENA MARLOW</span>
  <span style="left:600px;font-weight:400">VELARI</span>
  <span style="left:772px;font-weight:400">CLARA HUERTA</span>
  <span style="left:945px">CORSANO</span>
</section>

<section class="store">
  <h2 class="section-title" style="left:0;width:1200px;text-align:center;top:1540px;font-size:30px">Online Store</h2>
  <div class="card active" style="left:160px">
    <div class="img" role="img" aria-label="Black graduated frame glasses"></div>
    <div class="label">Graduated frame</div>
    <div class="price">€ 79,99</div>
    <div class="cart"><svg width="14" height="15" viewBox="0 0 14 15"><rect x="1" y="4" width="10" height="10" rx="1" fill="none" stroke="#fff" stroke-width="1.4"/><path d="M3.5 4V3a2.5 2.5 0 0 1 5 0v1" fill="none" stroke="#fff" stroke-width="1.4"/></svg></div>
    <div class="rule"></div>
  </div>
  <div class="card" style="left:390px">
    <div class="img" role="img" aria-label="Tortoiseshell aviator frame glasses"></div>
    <div class="label">Graduated frame</div>
    <div class="price">€149,99</div>
    <div class="cart"><svg width="14" height="15" viewBox="0 0 14 15"><rect x="1" y="4" width="10" height="10" rx="1" fill="none" stroke="#444" stroke-width="1.4"/><path d="M3.5 4V3a2.5 2.5 0 0 1 5 0v1" fill="none" stroke="#444" stroke-width="1.4"/></svg></div>
    <div class="rule"></div>
  </div>
  <div class="card" style="left:618px">
    <div class="img" role="img" aria-label="Blue round frame glasses"></div>
    <div class="label">Graduated frame</div>
    <div class="price">€149,99</div>
    <div class="cart"><svg width="14" height="15" viewBox="0 0 14 15"><rect x="1" y="4" width="10" height="10" rx="1" fill="none" stroke="#444" stroke-width="1.4"/><path d="M3.5 4V3a2.5 2.5 0 0 1 5 0v1" fill="none" stroke="#444" stroke-width="1.4"/></svg></div>
    <div class="rule"></div>
  </div>
  <div class="card" style="left:846px">
    <div class="img" role="img" aria-label="Brown round frame glasses"></div>
    <div class="label">Graduated frame</div>
    <div class="price">€149,99</div>
    <div class="cart"><svg width="14" height="15" viewBox="0 0 14 15"><rect x="1" y="4" width="10" height="10" rx="1" fill="none" stroke="#444" stroke-width="1.4"/><path d="M3.5 4V3a2.5 2.5 0 0 1 5 0v1" fill="none" stroke="#444" stroke-width="1.4"/></svg></div>
    <div class="rule"></div>
  </div>
</section>

<section class="channel">
  <div class="frame" style="left:250px;top:1991px;width:263px;height:232px;clip-path:polygon(0 85%,0 100%,100% 100%,100% 0,85% 0,85% 85%)"></div>
  <div class="photo-box" style="left:160px;top:1957px;width:306px;height:228px;background:linear-gradient(180deg,#1d1a16 0%,#3f6d74 40%,#b89c72 65%,#8d8378 100%)" role="img" aria-label="Store interior with teal display walls and a gold chandelier"></div>
  <h2 class="section-title" style="left:599px;top:1944px;font-size:31px">Follow us on Vidora</h2>
  <span class="tab" style="left:600px;color:var(--ink);border-bottom:2px solid var(--ink)">Vidora</span>
  <span class="tab" style="left:699px;color:#bbb;border-bottom:2px solid #ddd">UNBOXING</span>
  <span class="tab" style="left:802px;color:#bbb;border-bottom:2px solid #ddd">Short Videos</span>
  <p class="para" style="left:600px;top:2051px;font-weight:700;color:var(--ink)">Welcome to Vidora's</p>
  <p class="para" style="left:600px;top:2080px;width:440px">optics and optometry channel. We are here to advise, explain and guide you if you need any help related to the world of vision.</p>
  <p class="para" style="left:600px;top:2128px;width:440px">In the channel we will have advice, UNBOXING news, explanations with criteria and many collaborations of experts in this sector so that nothing escapes us.</p>
  <a class="btn" style="left:600px;top:2198px;width:81px;height:30px">More</a>
</section>

<footer class="footer">
  <div class="brand" style="left:160px;top:90px;width:140px">
    <div class="name">ORLA</div>
    <div class="sub">ÓPTICA MÉDICA</div>
  </div>
  <h3 class="foot-head" style="left:470px;top:58px">Contact Us</h3>
  <svg class="abs" style="left:470px;top:90px" width="12" height="16" viewBox="0 0 12 16"><path d="M6 0a6 6 0 0 0-6 6c0 4.5 6 10 6 10s6-5.5 6-10a6 6 0 0 0-6-6z" fill="#222"/><circle cx="6" cy="6" r="2.2" fill="#f4f4f4"/></svg>
  <p class="foot-line" style="left:494px;top:86px">Address Calle Olmeda, 22<br>Ribera</p>
  <svg class="abs" style="left:470px;top:140px" width="14" height="14" viewBox="0 0 14 14"><path d="M3 1l2.5 3-1.5 1.5c1 2 2.5 3.5 4.5 4.5L10 8.5l3 2.5-1.5 2C6 13 1 8 1 2.5z" fill="none" stroke="#d3a14a" stroke-width="1.3"/></svg>
  <p class="foot-line" style="left:494px;top:138px;color:var(--gold)">900 12 34 56</p>
  <svg class="abs" style="left:470px;top:178px" width="15" height="11" viewBox="0 0 15 11"><rect x="0.7" y="0.7" width="13.6" height="9.6" fill="none" stroke="#d3a14a" stroke-width="1.3"/><path d="M1 1l6.5 5L14 1" fill="none" stroke="#d3a14a" stroke-width="1.3"/></svg>
  <p class="foot-line" style="left:494px;top:175px;color:var(--gold)">info@orlaoptica.example</p>
  <h3 class="foot-head" style="left:841px;top:58px">Follow Us</h3>
</footer>
<div class="social" style="left:841px">
  <span>Nuvo</span><span>Trill</span><span>Orbi</span><span>Kavel</span><span>Pixa</span>
</div>
<div class="bottombar">Copyrights © 2018 Orla Optica Medica, allrights are Reserved.</div>

</body>
</html>
```